Veltra Metrics New Website for Health Benefits Plan Decisioneering Tool Launch

Veltra Metrics is a SaaS provider of health benefits comparison tools. We need a new simple SaaS focused website to direct customers to our product

Target Market(s)

General Public comparing their health benefits plans from their employer or from the state exchanges in the US

Coding

Coded - Design and coding required

Number of Pages Required

3 page

Requirements
Must have
• Main page - "Know the Best Health Benefits Plan for You!"
Graphic of a person looking over papers on their desk
Compare Now button to link to SaaS product
About Us
Product Page

https://plimbo.example/top-app-pages/

```html
<!DOCTYPE html>
<html lang="en">
<head>
<meta charset="utf-8">
<title>Veltra Metrics LLC</title>
<link href="https://fonts.googleapis.com/css2?family=Cinzel:wght@500;700&family=Montserrat:wght@400;500;600&display=swap" rel="stylesheet">
<style>
:root{
  --brand:#29a9e1;
  --brand-dark:#2793c0;
  --ink:#333333;
  --white:#ffffff;
  --paper:#f3ecd2;
}
*{box-sizing:border-box;margin:0;padding:0}
html,body{width:1200px;height:705px;overflow:hidden;background:var(--white)}
body{position:relative;font-family:"Montserrat",sans-serif;color:var(--ink)}
.site-header{position:absolute;left:0;top:0;width:1200px;height:96px;background:var(--white)}
.brand{position:absolute;left:141px;top:30px;display:flex;align-items:center;gap:10px;color:var(--brand);font-family:"Montserrat",sans-serif;font-weight:600;font-size:22px;line-height:1;white-space:nowrap}
.brand-dot{width:14px;height:14px;border-radius:50%;background:var(--brand)}
.main-nav{position:absolute;top:25px;right:141px;display:flex;align-items:center;height:39px}
.main-nav a{font-size:12.5px;font-weight:500;letter-spacing:.5px;color:var(--ink);text-decoration:none;margin-left:33px}
.main-nav a:first-child{margin-left:0}
.main-nav .nav-cta{background:var(--brand);color:var(--white);height:39px;width:135px;display:flex;align-items:center;justify-content:center;border-radius:3px;margin-left:32px}
.hero{position:absolute;left:0;top:96px;width:1200px;height:517px;background:var(--brand)}
.hero-title{position:absolute;left:141px;top:155px;font-family:"Cinzel",serif;font-weight:700;font-size:36px;line-height:46px;color:var(--white);letter-spacing:.5px;white-space:nowrap}
.hero-cta{position:absolute;left:141px;top:318px;width:162px;height:42px;background:var(--white);color:var(--brand);border-radius:3px;display:flex;align-items:center;justify-content:center;font-size:13.5px;font-weight:500;letter-spacing:.6px;text-decoration:none}
.hero-art{position:absolute;left:541px;top:128px;width:562px;height:389px;background:linear-gradient(160deg,#3c4047 0%,#4f5a5c 35%,#9fd6d8 65%,#e21b6a 85%,var(--paper) 100%);opacity:.85;border-radius:4px 4px 0 0}
.hero-band{position:absolute;left:0;top:613px;width:1200px;height:25px;background:var(--brand-dark)}
.site-footer{position:absolute;left:0;top:638px;width:1200px;height:67px}
.copyright{position:absolute;left:143px;top:26px;font-size:12.5px;color:var(--ink)}
.social{position:absolute;right:141px;top:17px;display:flex;gap:8px}
.social a{width:35px;height:35px;border-radius:50%;display:block}
.social .s1{background:#3b5a99}
.social .s2{background:#c9283c}
.social .s3{background:#70c4ef}
.social .s4{background:#e4171d}
</style>
</head>
<body>
<header class="site-header">
  <div class="brand"><span class="brand-dot"></span><span class="brand-name">Veltra Metrics LLC</span></div>
  <nav class="main-nav">
    <a href="#">HOME</a>
    <a href="#">ABOUT US</a>
    <a href="#">PRODUCT</a>
    <a href="#" class="nav-cta">CONTACT US</a>
  </nav>
</header>
<section class="hero">
  <h1 class="hero-title">KNOW THE BEST<br>HEALTH BENEFITS<br>PLAN FOR YOU!</h1>
  <a class="hero-cta" href="https://plimbo.example/top-app-pages/">COMPARE NOW</a>
  <div class="hero-art" role="img" aria-label="Illustration of a person at a desk with a computer, reviewing stacks of papers and binders"></div>
</section>
<div class="hero-band"></div>
<footer class="site-footer">
  <p class="copyright">Copyright © 2020 VELTRA METRICS LLC. All Rights Reserved.</p>
  <div class="social">
    <a href="#" class="s1" aria-label="Social profile 1"></a>
    <a href="#" class="s2" aria-label="Social profile 2"></a>
    <a href="#" class="s3" aria-label="Social profile 3"></a>
    <a href="#" class="s4" aria-label="Social profile 4"></a>
  </div>
</footer>
</body>
</html>
```